Events publishing website

Have increased the budget for Coded website design. Thanks
-
We need a wordpress website for events publishing. The website will be using all different kinds of events (social, business, music etc). The website should allow user to submit the new events. the new events will be published after admin reviewed.
Key menu items & requirements
- New Events (1-show picture, short description & start/end date. User can view more details in another page. 2-have categories, such as locations, free/ticked, event type etc. 3 - allow user to share the events in social website)
- Event organizer list (show the full list and most popular event organizers. users can view the list by categories, similar to above)
- events establishments (allow user to publish events related informations such as equipments, venue informations etc)
- discussion forum
Key functions
-registration page (new users should fill name, location, normal users or event organizer, types of event organizer etc)
-allow user to change locations to view different events
-search function
The functions should be similar to the following, the design should not. The website should not look like a proper website.
http://www.plavorgatherings.example
Reason: Hi All, have extended few days to allow some changes to be made for current design. Thanks

```html
<!DOCTYPE html>
<html lang="en">
<head>
<meta charset="utf-8">
<title>Events – Event Organizers</title>
<link rel="stylesheet" href="https://fonts.googleapis.com/css2?family=Cuprum:wght@400;700&family=Open+Sans:wght@400;600&display=swap">
<style>
:root{
  --black:#111;
  --teal:#4f8c80;
  --teal-dark:#3b7166;
  --teal-light:#6aa496;
  --teal-text:#2f7f70;
  --orange:#f5ae42;
  --orange-dark:#e89a1e;
  --paper:#fff;
  --sand:#ecebe5;
  --ink:#1d1d1d;
  --muted:#555;
  --rule:#b9b9b9;
}
*{box-sizing:border-box;margin:0;padding:0}
html,body{width:1200px;height:2932px;overflow:hidden}
body{position:relative;background:var(--sand);font-family:"Open Sans",Arial,sans-serif;color:var(--ink)}
.page-top{position:absolute;left:0;top:0;width:1200px;height:553px;
  background:radial-gradient(ellipse at 160px 60px,#fff 0,#fff 30%,#f1f2ee 70%,#e9eae4 100%)}
.utility-bar{position:absolute;left:0;top:0;width:1200px;height:38px;background:var(--black);
  display:flex;align-items:center;padding-left:34px;font-size:12px;color:#fff;letter-spacing:.2px}
.utility-bar span{padding:0 10px}
.utility-bar span:first-child{padding-left:0}
.utility-bar i{font-style:normal;color:#aaa}
.brand{position:absolute;left:47px;top:72px;font-family:"Cuprum",sans-serif;color:var(--teal-text)}
.brand-name{font-size:44px;line-height:44px}
.brand-slogan{font-size:17px;margin-top:2px}
.account-links{position:absolute;left:852px;top:58px;display:flex;gap:22px;font-family:"Cuprum",sans-serif;font-size:16px;color:#333}
.account-links span{display:flex;align-items:center;gap:6px}
.search{position:absolute;left:835px;top:109px;display:flex;gap:4px}
.search-field{width:299px;height:39px;border:1px solid #ccc;background:#fff;font-size:13px;color:#666;padding:10px 12px}
.search-go{width:38px;height:39px;background:var(--orange);color:#fff;font-size:14px;font-weight:600;display:flex;align-items:center;justify-content:center}
.main-nav{position:absolute;left:35px;top:172px;width:1145px;height:63px;
  background:linear-gradient(#5f9a8d,#3f7a6e);display:flex;box-shadow:0 2px 3px rgba(0,0,0,.25)}
.main-nav a{font-family:"Cuprum",sans-serif;font-size:20px;color:#fff;text-decoration:none;
  display:flex;align-items:center;justify-content:center;border-right:1px solid #2f6157;box-shadow:1px 0 0 #79ad9f}
.hero{position:absolute;left:35px;top:238px;width:1145px;height:356px;
  background:linear-gradient(100deg,#2a2f3a 0%,#4e6a78 25%,#3b2a22 50%,#b5541f 70%,#e8962b 85%,#7a2e14 100%)}
.hero-arrow{position:absolute;top:378px;width:46px;height:46px;border-radius:50%;background:#f3f3f3;
  box-shadow:0 0 3px rgba(0,0,0,.3);display:flex;align-items:center;justify-content:center}
.content{position:absolute;left:47px;top:602px;width:1120px;height:1949px;background:var(--paper);
  border:1px solid #ddd;box-shadow:0 0 4px rgba(0,0,0,.12)}
.content-divider{position:absolute;left:-47px;top:117px;width:1200px;border-top:1px solid #d4d4d4}
.section-title{position:absolute;left:35px;top:48px;font-family:"Cuprum",sans-serif;font-weight:400;font-size:20px;color:#222}
.section-title::after{content:"";position:absolute;left:0;top:40px;width:207px;border-top:2px dotted #888}
.location-select{position:absolute;left:760px;top:22px;width:258px;height:33px;border:2px solid #cfcfcf;border-radius:18px;
  font-size:13px;color:#888;padding:6px 16px;display:flex;justify-content:space-between;align-items:center}
.location-go{position:absolute;left:1026px;top:15px;width:45px;height:45px;border-radius:50%;background:#1a1a1a;
  border:2px solid #999;color:#fff;font-family:"Cuprum",sans-serif;font-size:20px;display:flex;align-items:center;justify-content:center}
.organizer{position:absolute;left:35px;width:1060px;height:530px}
.organizer-photo{position:absolute;left:0;top:0;width:372px;height:223px;border:4px solid #fff;box-shadow:0 0 3px rgba(0,0,0,.45)}
.organizer-details{position:absolute;left:316px;top:10px;width:750px;display:grid;
  grid-template-columns:243px 1fr;column-gap:14px;
  grid-template-rows:27px 24px 31px 33px 49px 37px 41px 125px 39px 41px 30px;
  font-size:12px;line-height:19px}
.organizer-details dt{grid-column:1;text-align:right;font-family:"Cuprum",sans-serif;font-weight:400;font-size:18px;line-height:22px;color:#111;white-space:nowrap}
.organizer-details dd{grid-column:2;overflow:hidden}
.organizer-details .performance-text{padding-top:2px}
.venue-title{font-family:"Cuprum",sans-serif;font-weight:400;font-size:20px;line-height:22px;color:#111;white-space:nowrap}
.photo-slot{width:104px;height:108px;background:var(--orange);margin-top:-6px}
.more-link{position:absolute;right:26px;top:487px;font-family:"Cuprum",sans-serif;font-size:15px;color:var(--teal-text)}
.more-link small{font-size:11px;margin-left:6px}
.organizer-rule{position:absolute;left:-2px;top:508px;width:1055px;border-top:2px dotted var(--rule)}
.pagination{position:absolute;display:flex;align-items:center;gap:11px;font-size:15px}
.pagination .current{width:25px;height:25px;border-radius:50%;background:var(--teal);color:#fff;display:flex;align-items:center;justify-content:center}
.pagination .next{margin-left:12px}
.footer{position:absolute;left:35px;top:2567px;width:1145px;height:365px;background:linear-gradient(#5a9588,#3c7467);color:#fff}
.footer h3{position:absolute;font-family:"Cuprum",sans-serif;font-weight:400;font-size:21px}
.quick-links{position:absolute;left:49px;top:63px;width:650px;display:grid;grid-template-columns:127px 166px 162px 1fr;font-size:13px}
.quick-links span{height:33px;line-height:30px;padding-left:6px;border-bottom:1px dashed #8fbcb1}
.social{position:absolute;left:782px;top:63px;display:flex;gap:9px}
.social span{width:30px;height:30px;border-radius:50%;background:#fff}
.copyright{position:absolute;left:24px;top:244px;width:1098px;height:55px;background:#3a6e63;font-size:11px;padding:20px 24px;color:#e6f0ed}
</style>
</head>
<body>
<div class="page-top"></div>

<nav class="utility-bar">
  <span>EVENTS</span><i>|</i><span>NEWS EVENTS</span><i>|</i><span>SAVOUR</span><i>|</i><span>EVENT INTERNATIONAL ART SERIES</span><i>|</i><span>NSW EVENTS CALENDAR</span>
</nav>

<header>
  <div class="brand"><div class="brand-name">Events</div><div class="brand-slogan">your company slogan here</div></div>
  <div class="account-links">
    <span><svg width="20" height="20" viewBox="0 0 20 20"><path d="M2 9h4v10H2zM7 18V9l4-8c2 0 2 2 2 3l-1 4h6c1 0 2 1 1 3l-2 6c0 1-1 1-2 1z" fill="#333"/></svg>SIGN UP</span>
    <span><svg width="18" height="22" viewBox="0 0 18 22"><path d="M4 10V6a5 5 0 0 1 10 0v4h-3V6a2 2 0 0 0-4 0v4z" fill="#333"/><rect x="1" y="10" width="16" height="12" rx="2" fill="#333"/></svg>LOGIN</span>
    <span><svg width="26" height="22" viewBox="0 0 26 22"><circle cx="13" cy="6" r="5.5" fill="#333"/><path d="M2 22c0-7 5-10 11-10s11 3 11 10z" fill="#333"/></svg>MEMBER</span>
  </div>
  <div class="search"><div class="search-field">Enter Keyword here</div><div class="search-go">Go</div></div>
</header>

<nav class="main-nav">
  <a style="width:114px">MAIN</a><a style="width:150px">POPULAR</a><a style="width:225px">EVENT ORGANIZER</a><a style="width:117px">FORUM</a><a style="width:121px">HELP</a><a style="width:140px;border:0;box-shadow:none">CONTACT US</a>
</nav>

<div class="hero" role="img" aria-label="Photo of an empty conference hall with stage screens and warm orange stage lighting"></div>
<div class="hero-arrow" style="left:22px"><svg width="12" height="18" viewBox="0 0 12 18"><path d="M10 2 3 9l7 7" stroke="#888" stroke-width="2.5" fill="none"/></svg></div>
<div class="hero-arrow" style="left:1148px"><svg width="12" height="18" viewBox="0 0 12 18"><path d="m2 2 7 7-7 7" stroke="#888" stroke-width="2.5" fill="none"/></svg></div>

<main class="content">
  <div class="content-divider"></div>
  <h2 class="section-title">Events Organizer</h2>
  <div class="location-select">Area/ Location <svg width="12" height="9" viewBox="0 0 12 9"><path d="M0 0h12L6 9z" fill="#111"/></svg></div>
  <div class="location-go">GO</div>

  <article class="organizer" style="top:139px">
    <div class="organizer-photo" role="img" aria-label="Photo of dancers performing on a colourfully lit stage" style="background:linear-gradient(120deg,#1f7a3a,#8a2f7a 45%,#d98a1a 75%,#3a1a2a)"></div>
    <dl class="organizer-details">
      <dt>Show The Venue :</dt><dd class="venue-title">Sydney Treasure Hunt on the Monorail</dd>
      <dt></dt><dd>Any Monorail Station</dd>
      <dt></dt><dd>Chicago, IL</dd>
      <dt>Date :</dt><dd>20 July 2012</dd>
      <dt>Performance :</dt><dd class="performance-text">E-Commerce is a major progress in technology that has changed the way in which the customers now purchase information, products and the services. I</dd>
      <dt>Speaker :</dt><dd>Marco Hale</dd>
      <dt>*name :</dt><dd>David</dd>
      <dt>*photo :</dt><dd><div class="photo-slot"></div></dd>
      <dt>*specialty :</dt><dd>Sydney Treasure Hunt on the Monorail</dd>
      <dt>*area/location :</dt><dd>Any Monorail Station , Chicago, IL</dd>
      <dt>*contact numbers :</dt><dd>055 0100 2834</dd>
    </dl>
    <div class="more-link">Clickhere<small>&gt;&gt;</small></div>
    <div class="organizer-rule"></div>
  </article>

  <article class="organizer" style="top:679px">
    <div class="organizer-photo" role="img" aria-label="Photo of performers on a dark stage under blue spotlights" style="background:linear-gradient(120deg,#0a0a1a,#1c2a6a 45%,#6a3a8a 70%,#0a0a14)"></div>
    <dl class="organizer-details">
      <dt>Show The Venue :</dt><dd class="venue-title">Sydney Treasure Hunt on the Monorail</dd>
      <dt></dt><dd>Any Monorail Station</dd>
      <dt></dt><dd>Chicago, IL</dd>
      <dt>Date :</dt><dd>20 July 2012</dd>
      <dt>Performance :</dt><dd class="performance-text">E-Commerce is a major progress in technology that has changed the way in which the customers now purchase information, products and the services. I</dd>
      <dt>Speaker :</dt><dd>Marco Hale</dd>
      <dt>*name :</dt><dd>David</dd>
      <dt>*photo :</dt><dd><div class="photo-slot"></div></dd>
      <dt>*specialty :</dt><dd>Sydney Treasure Hunt on the Monorail</dd>
      <dt>*area/location :</dt><dd>Any Monorail Station , Chicago, IL</dd>
      <dt>*contact numbers :</dt><dd>055 0100 2834</dd>
    </dl>
    <div class="more-link">Clickhere<small>&gt;&gt;</small></div>
    <div class="organizer-rule" style="top:546px"></div>
  </article>

  <article class="organizer" style="top:1266px;left:63px">
    <div class="organizer-photo" role="img" aria-label="Photo of an outdoor evening banquet with tables lit in blue" style="background:linear-gradient(170deg,#0d1a2a,#1e3e2a 40%,#3a52b8 70%,#c8d0f0)"></div>
    <dl class="organizer-details">
      <dt>Show The Venue :</dt><dd class="venue-title">Sydney Treasure Hunt on the Monorail</dd>
      <dt></dt><dd>Any Monorail Station</dd>
      <dt></dt><dd>Chicago, IL</dd>
      <dt>Date :</dt><dd>20 July 2012</dd>
      <dt>Performance :</dt><dd class="performance-text">E-Commerce is a major progress in technology that has changed the way in which the customers now purchase information, products and the services. I</dd>
      <dt>Speaker :</dt><dd>Marco Hale</dd>
      <dt>*name :</dt><dd>David</dd>
      <dt>*photo :</dt><dd><div class="photo-slot"></div></dd>
      <dt>*specialty :</dt><dd>Sydney Treasure Hunt on the Monorail</dd>
      <dt>*area/location :</dt><dd>Any Monorail Station , Chicago, IL</dd>
      <dt>*contact numbers :</dt><dd>055 0100 2834</dd>
    </dl>
    <div class="more-link" style="top:547px;right:20px">Clickhere<small>&gt;&gt;</small></div>
  </article>

  <div class="pagination" style="left:841px;top:1874px">
    <span class="current">1</span><span>2</span><span>3</span><span>4</span><span>5</span><span>6</span><span>7</span><span>8</span><span class="next">Next</span>
  </div>
</main>

<footer class="footer">
  <h3 style="left:49px;top:18px">Quick Links</h3>
  <div class="quick-links">
    <span>Hom page</span><span>Login</span><span>Support</span><span>Term &amp; Conditions of Use</span>
    <span>Events</span><span>FAQ</span><span>Add Events</span><span>Privacy Policy</span>
    <span>Popular</span><span>Login</span><span>Speical Events</span><span>Help</span>
    <span>News</span><span>Forgot Password</span><span>Contact info</span><span></span>
  </div>
  <h3 style="left:764px;top:18px">Connect with Us</h3>
  <div class="social"><span></span><span></span><span></span></div>
  <div class="copyright">© 2012 Company Name &nbsp;|&nbsp; All right reserved &nbsp;|&nbsp; Policy Privacy</div>
</footer>
</body>
</html>
```